Job Recruiting Agemcy

almost like my current site www.plorvex.com but with these changes see and what i meant about the across the to the site says home job companies categories pages blog and login sign up that should only be the 4 i said only 1 home 2 industries 3 jobs 4 contact us. and remove latest blog post and our partners because that's not us we have to post acuarte information thanks and the name of the company if your using is is work and careful hiring partners and want it easy for us to post and remove jobs and where it emails us every resume or person that applies

Requirements
Must have
• must send email to us when an application is submitted and try to incorparate the colors of current site
Nice to have
• i want a pretty basic site for now just like the one i have but with all thats above were its easy for me being the own to be able to post jobs and everything

```html
<!DOCTYPE html>
<html lang="en">
<head>
<meta charset="utf-8">
<title>Plorvex — Work and careful hiring partners</title>
<link href="https://fonts.googleapis.com/css2?family=Cabin:wght@400;500;600&display=swap" rel="stylesheet">
<style>
:root{
  --pink:#d84457;
  --magenta:#c8405a;
  --violet:#6a0fc0;
  --plum:#53156b;
  --wine:#7d1753;
  --link:#5a16c0;
  --green:#2f6b47;
  --band-green:#3f7a59;
  --ink:#1d1d1d;
  --soft:#e8e8e8;
  --footer:#1e1e22;
  --white:#ffffff;
}
*{box-sizing:border-box;margin:0;padding:0}
html,body{width:1200px;height:3391px;overflow:hidden;background:var(--white)}
body{font-family:"Cabin",sans-serif;color:var(--ink);position:relative}
.abs{position:absolute}
/* header */
.site-header{position:absolute;left:0;top:0;width:1200px;height:134px;background:var(--white);z-index:3}
.auth-btn{position:absolute;top:18px;height:36px;border:1.5px solid var(--link);color:var(--link);font-size:15px;line-height:33px;text-align:center;border-radius:2px}
.auth-login{left:865px;width:83px}
.auth-signup{left:964px;width:91px}
.main-nav{position:absolute;top:91px;left:683px;display:flex;gap:36px;font-size:15px}
.main-nav span{color:#222}
.main-nav .current{color:var(--magenta)}
.brand-tab{position:absolute;left:88px;top:0;z-index:4}
.brand-name{position:absolute;left:0;top:124px;width:204px;text-align:center;font-size:24px;font-weight:600;color:var(--plum);letter-spacing:1px}
.brand-dot{position:absolute;left:86px;top:30px;width:32px;height:32px;background:var(--plum);border-radius:50%}
.brand-tag{position:absolute;left:0;top:153px;width:204px;text-align:center;font-size:7px;color:var(--ink)}
/* hero */
.hero{position:absolute;left:0;top:134px;width:1200px;height:616px}
.hero-title{position:absolute;left:144px;top:182px;width:394px;text-align:center;color:#fff;font-size:38px;font-weight:500}
.field{position:absolute;left:144px;width:394px;height:47px;background:#fff;font-size:15px;line-height:47px;padding-left:22px;color:#222}
.field svg{position:absolute;right:14px;top:13px}
.search-btn{position:absolute;left:144px;top:368px;width:394px;height:48px;background:#111;color:#fff;font-size:22px;line-height:48px;text-align:center}
/* intro */
.intro{position:absolute;left:130px;top:816px;width:940px;text-align:center;font-size:27px;line-height:46px;color:#1d1d1d}
.section-title{position:absolute;left:0;width:1200px;text-align:center;font-size:33px;font-weight:500;color:var(--green)}
/* industries */
.industry{position:absolute;top:1202px;width:217px;height:216px;color:#fff;text-align:center}
.industry .count{position:absolute;left:88px;top:-20px;width:40px;height:40px;border-radius:50%;background:#222;font-size:12px;line-height:40px}
.industry svg{position:absolute;left:78px;top:38px}
.industry h3{position:absolute;top:118px;left:0;width:100%;font-size:23px;font-weight:500}
.industry p{position:absolute;top:155px;left:18px;right:18px;font-size:11.5px;line-height:19px}
/* jobs */
.job-card{position:absolute;width:297px;height:200px;background:#fff;padding:18px 20px}
.job-card h4{font-size:15px;font-weight:400;line-height:24px;color:var(--link);height:52px}
.job-card p{font-size:10.5px;line-height:19px;color:#333;margin-top:6px}
.apply{position:absolute;left:20px;bottom:20px;height:38px;padding:0 14px;border:1px solid var(--magenta);color:var(--magenta);font-size:13.5px;line-height:36px}
.view-all{position:absolute;left:550px;top:2163px;width:100px;height:35px;background:#111;color:#fff;font-size:15px;line-height:35px;text-align:center}
/* testimonials */
.quote-card{position:absolute;top:2468px;width:298px;height:192px;background:var(--soft);padding:22px 24px;font-size:14.5px;line-height:27px;color:#222}
.quote-card svg{display:block;margin-bottom:10px}
.person{position:absolute;top:2682px;width:298px;height:64px}
.avatar{position:absolute;left:0;top:0;width:64px;height:64px;border-radius:50%;background:radial-gradient(circle at 50% 40%,#c9b4a3,#8d7f76)}
.person b{position:absolute;left:73px;top:14px;font-weight:400;font-size:15px;color:#222}
.person small{position:absolute;left:73px;top:38px;font-size:11px;color:#444}
/* seek */
.seek-sub{position:absolute;left:0;top:3031px;width:1200px;text-align:center;font-size:19px;color:#222}
.outline-btn{position:absolute;top:3078px;height:36px;border:1.5px solid var(--link);color:var(--link);font-size:16px;line-height:33px;text-align:center}
/* footer */
.foot-links{position:absolute;left:145px;top:3293px;font-size:11.5px;color:#bbb;word-spacing:2px}
.foot-copy{position:absolute;left:145px;top:3326px;font-size:11.5px;color:#bbb}
.social{position:absolute;top:3302px;width:22px;height:22px;border-radius:50%;background:#9a9a9a}
</style>
</head>
<body>

<header class="site-header">
  <div class="auth-btn auth-login">LOG IN</div>
  <div class="auth-btn auth-signup">SIGN UP</div>
  <nav class="main-nav"><span class="current">HOME</span><span>INDUSTRIES</span><span>JOBS</span><span>CONTACT US</span></nav>
</header>

<div class="brand-tab">
  <svg width="204" height="222" viewBox="0 0 204 222"><path d="M0 0H204V134L102 220L0 134Z" fill="#fff"/></svg>
  <div class="brand-dot"></div>
  <div class="brand-name">PLORVEX</div>
  <div class="brand-tag">WORK AND CAREFUL HIRING PARTNERS</div>
</div>

<section class="hero">
  <svg class="abs" style="left:0;top:0" width="1200" height="616" viewBox="0 0 1200 616">
    <defs>
      <linearGradient id="photoTone" x1="0" y1="0" x2="1" y2="1">
        <stop offset="0" stop-color="#a9b2bb"/><stop offset=".5" stop-color="#6f7780"/><stop offset="1" stop-color="#3c4550"/>
      </linearGradient>
      <linearGradient id="heroShade" x1="0" y1="0" x2="0" y2="1">
        <stop offset="0" stop-color="#d8466a"/><stop offset=".5" stop-color="#9d23b5"/><stop offset="1" stop-color="#7313d6"/>
      </linearGradient>
    </defs>
    <path role="img" aria-label="Photo of a smiling recruiter in a meeting with a candidate" d="M0 0H1200V616L0 544Z" fill="url(#photoTone)"/>
    <path d="M0 0H460C560 90 610 260 590 400C580 480 560 520 540 560L0 544Z" fill="url(#heroShade)" opacity=".95"/>
    <path d="M70 378l-10 12 10 12" stroke="#fff" stroke-width="3" fill="none"/>
    <path d="M1130 378l10 12-10 12" stroke="#fff" stroke-width="3" fill="none"/>
  </svg>
  <h1 class="hero-title">Your career starts here!</h1>
  <div class="field" style="top:241px">Keywords
    <svg width="22" height="22" viewBox="0 0 22 22"><circle cx="9" cy="9" r="7" stroke="#111" stroke-width="2.6" fill="none"/><path d="M14 14l6 6" stroke="#111" stroke-width="3"/></svg>
  </div>
  <div class="field" style="top:304px">Location
    <svg width="16" height="22" viewBox="0 0 16 22"><path d="M8 1a7 7 0 0 0-7 7c0 5 7 13 7 13s7-8 7-13a7 7 0 0 0-7-7z" fill="#111"/><circle cx="8" cy="8" r="2.6" fill="#fff"/></svg>
  </div>
  <div class="search-btn">SEARCH NOW</div>
</section>

<p class="intro">We have over 35 years of Specialized Recruiting and souring experience. We cover a broad spectrum of industries to include some of the top aerospace and pharmaceutical commercial companies of today.</p>

<svg class="abs" style="left:144px;top:1004px" width="912" height="54" viewBox="0 0 912 54">
  <line x1="0" y1="27" x2="430" y2="27" stroke="#5a4a8a" stroke-width="1"/>
  <line x1="482" y1="27" x2="912" y2="27" stroke="#5a4a8a" stroke-width="1"/>
  <circle cx="456" cy="27" r="10" fill="#9a2fb5"/>
</svg>

<h2 class="section-title" style="top:1112px">Industries we support</h2>

<div class="industry" style="left:144px;background:var(--pink)">
  <div class="count">52</div>
  <svg width="60" height="60" viewBox="0 0 60 60" fill="none" stroke="#fff" stroke-width="2"><path d="M30 4c3 0 4 4 4 8v12l22 12v5l-22-6v12l7 6v3l-11-3-11 3v-3l7-6V35L4 41v-5l22-12V12c0-4 1-8 4-8z"/></svg>
  <h3>Aero Space</h3>
  <p>Norvane Avionics, Skylark Orbital, Veltra Power</p>
</div>
<div class="industry" style="left:375px;background:var(--violet)">
  <div class="count">60</div>
  <svg width="60" height="60" viewBox="0 0 60 60" fill="none" stroke="#fff" stroke-width="2"><rect x="12" y="4" width="24" height="8" rx="2"/><path d="M14 12v4l-4 6v32h28V22l-4-6v-4"/><path d="M24 28v12M18 34h12"/><circle cx="46" cy="44" r="9"/></svg>
  <h3>Pharmaceutical</h3>
  <p>Quenra Bio Labs, Lumessa Care</p>
</div>
<div class="industry" style="left:607px;background:var(--plum)">
  <div class="count">85</div>
  <svg width="66" height="60" viewBox="0 0 66 60" fill="none" stroke="#fff" stroke-width="2"><rect x="2" y="14" width="38" height="28"/><path d="M40 22h14l10 12v8H40z"/><circle cx="14" cy="46" r="5"/><circle cx="52" cy="46" r="5"/></svg>
  <h3>Transportation</h3>
  <p>Harlow Freight, Tandro Parcel</p>
</div>
<div class="industry" style="left:837px;background:var(--wine)">
  <div class="count">61</div>
  <svg width="60" height="60" viewBox="0 0 60 60" fill="none" stroke="#fff" stroke-width="2"><path d="M30 6v50"/><circle cx="30" cy="8" r="3"/><path d="M30 14c-14-6-24-2-26 2 8 2 18 2 26 4 8-2 18-2 26-4-2-4-12-8-26-2z"/><path d="M36 24c-12 2-12 8 0 10-12 2-12 8 0 10"/></svg>
  <h3>Medical</h3>
  <p>Medivo, Corlith</p>
</div>

<svg role="img" aria-label="Green-toned photo of an open office" class="abs" style="left:0;top:1522px" width="1200" height="808" viewBox="0 0 1200 808">
  <defs><linearGradient id="officeTone" x1="0" y1="0" x2="1" y2="1"><stop offset="0" stop-color="#4a8563"/><stop offset="1" stop-color="#346b4c"/></linearGradient></defs>
  <path d="M0 0L1200 70V808L0 738Z" fill="url(#officeTone)"/>
</svg>
<h2 class="section-title" style="top:1665px;color:#fff">Recent Jobs</h2>

<div class="job-card" style="left:144px;top:1726px"><h4>Maecenas vel tortor accumsan quam varius imperdiet facilisis.</h4><p>Vivamus lacus justo, ultrices nec erat in, euismod iaculis mauris. Vivamus eleifend vitae nulla vel malesuada. In ac malesuada lacus.</p><div class="apply">APPLY NOW</div></div>
<div class="job-card" style="left:451px;top:1726px"><h4>Phasellus nisl est, condimentum vitae faucibus sollicitudin</h4><p>Vivamus lacus justo, ultrices nec erat in, euismod iaculis mauris. Vivamus eleifend vitae nulla vel malesuada. In ac malesuada lacus.</p><div class="apply">APPLY NOW</div></div>
<div class="job-card" style="left:758px;top:1726px"><h4>Curabitur ac elit leo. In eleifend dui tellus, in scelerisque elit porttitor</h4><p>Vivamus lacus justo, ultrices nec erat in, euismod iaculis mauris. Vivamus eleifend vitae nulla vel malesuada. In ac malesuada lacus.</p><div class="apply">APPLY NOW</div></div>
<div class="job-card" style="left:144px;top:1936px"><h4>Aenean sed quam sapien faucibus consequat</h4><p>Vivamus lacus justo, ultrices nec erat in, euismod iaculis mauris. Vivamus eleifend vitae nulla vel malesuada. In ac malesuada lacus.</p><div class="apply">APPLY NOW</div></div>
<div class="job-card" style="left:451px;top:1936px"><h4>Praesent quis risus mi. In mollis nulla in pulvinar dictum</h4><p>Vivamus lacus justo, ultrices nec erat in, euismod iaculis mauris. Vivamus eleifend vitae nulla vel malesuada. In ac malesuada lacus.</p><div class="apply">APPLY NOW</div></div>
<div class="job-card" style="left:758px;top:1936px"><h4>Vivamus interdum sagittis felis, ut dapibus ligula feugiat ac</h4><p>Vivamus lacus justo, ultrices nec erat in, euismod iaculis mauris. Vivamus eleifend vitae nulla vel malesuada. In ac malesuada lacus.</p><div class="apply">APPLY NOW</div></div>
<div class="view-all">VIEW ALL</div>

<h2 class="section-title" style="top:2401px">Testimonials</h2>

<svg class="abs" style="left:52px;top:2592px" width="1100" height="34" viewBox="0 0 1100 34">
  <path d="M17 4L5 17l12 13" stroke="#777" stroke-width="3" fill="none"/>
  <path d="M1081 4l12 13-12 13" stroke="#777" stroke-width="3" fill="none"/>
</svg>

<div class="quote-card" style="left:145px"><svg width="24" height="18" viewBox="0 0 24 18" fill="#8a8a8a"><path d="M0 18V9C0 3 3 0 9 0v4C6 4 5 6 5 8h5v10zM14 18V9c0-6 3-9 9-9v4c-3 0-4 2-4 4h5v10z"/></svg>I didn't even need training. I couldn't have asked for more than this. It really saves me time and effort. Plorvex is exactly what our business has</div>
<div class="quote-card" style="left:452px"><svg width="24" height="18" viewBox="0 0 24 18" fill="#8a8a8a"><path d="M0 18V9C0 3 3 0 9 0v4C6 4 5 6 5 8h5v10zM14 18V9c0-6 3-9 9-9v4c-3 0-4 2-4 4h5v10z"/></svg>I just can't get enough of Plorvex. I want to get a T-Shirt with Plorvex on it so I can show it off to everyone. This is simply unbelievable!</div>
<div class="quote-card" style="left:759px"><svg width="24" height="18" viewBox="0 0 24 18" fill="#8a8a8a"><path d="M0 18V9C0 3 3 0 9 0v4C6 4 5 6 5 8h5v10zM14 18V9c0-6 3-9 9-9v4c-3 0-4 2-4 4h5v10z"/></svg>Thanks for the great service. Plorvex has completely surpassed our expec­tations. Plorvex is the most valuable business resource we have ever pur-</div>

<div class="person" style="left:145px"><div class="avatar" role="img" aria-label="Portrait photo of the reviewer"></div><b>Rhea Dalton</b><small>HR Manager in Orchard Labs</small></div>
<div class="person" style="left:452px"><div class="avatar" role="img" aria-label="Portrait photo of the reviewer"></div><b>Marten Ilves</b><small>Key Account Manager in Chirpway Inc.</small></div>
<div class="person" style="left:759px"><div class="avatar" role="img" aria-label="Portrait photo of the reviewer"></div><b>Tobias Wrenfield</b><small>Brand Manager in Bidora Inc.</small></div>

<svg class="abs" style="left:0;top:2830px" width="1200" height="561" viewBox="0 0 1200 561">
  <path d="M0 0L1200 70V561H0Z" fill="#e9e9e9"/>
  <path d="M0 360L1200 435V561H0Z" fill="var(--footer)"/>
</svg>
<h2 class="section-title" style="top:2970px">Seeking For a Job?</h2>
<p class="seek-sub">Browse hundreds of job offers and find the best suitable position.</p>
<div class="outline-btn" style="left:453px;width:139px">SEARCH JOBS</div>
<div class="outline-btn" style="left:607px;width:140px">ADD A RESUME</div>

<footer>
  <div class="foot-links">Home &nbsp;|&nbsp; Industries &nbsp;|&nbsp; Jobs &nbsp;|&nbsp; Contact us &nbsp;|&nbsp; Login &nbsp;|&nbsp; Signup</div>
  <div class="foot-copy">Copyright © 2020 &nbsp;Plorvex. &nbsp;All rights reserved.</div>
  <div class="social" style="left:991px"></div>
  <div class="social" style="left:1033px"></div>
</footer>

</body>
</html>
```